Sophisticated, clean website reflecting my feminine, playful side to sell my abstract art,

I need a website no more than 3 pages to showcase my paintings, a little about me and some contact info. I do abstracts so looking for something a little edgy, yet feminine and current.
Updates

Hi there, These are some artists websites that I Iike: Marnelvoss.com (I like how airy it is) peterwallombry.com garethpolvens.com (I like how it scrolls) I'll need a place for a photo ( a headshot-i do not have it yet so I'll need to be able to upload that later) as well as an area for my bio. Also, it's important that I will be able to upload any new photos and descriptions easily so it should be user friendly. Lastly, I like in a sunny place so would like to have this seem upbeat and playful as that is how i like to paint. thanks-I'm trying to upload my photos now -

Target Market(s)

ppl ages 35-70 who want large scale art for their homes

Industry/Entity Type

art

Coding

Coded - Design and coding required

Number of Pages Required

3 page

Colors

Designer to choose colors to be used in the design.

Requirements
Must have
• photos of my art, a place for my bio, be easy to reach me. tasteful-nothing too "in your face" -my clients are pretty high end and organized. They like clean lines
Nice to have
• sophisticated background, muted tones in the back-similar clean font throughout-no cursive
Should not have
• too many dark areas. Too many blocks of color. Too serious.

```html
<!DOCTYPE html>
<html lang="en">
<head>
<meta charset="utf-8">
<title>Contact — Maren Holloway</title>
<link rel="stylesheet" href="https://fonts.googleapis.com/css2?family=Oswald:wght@300;400&family=Open+Sans:wght@400;600&family=Nunito:wght@400&family=Montserrat:wght@700&display=swap">
<style>
  :root {
    --ink: #111111;
    --muted: #666666;
    --gold: #a39a6a;
    --rule: #c9c3a2;
    --field-border: #dddddd;
    --mark-dark: #1b1d1b;
    --icon: #3a3a3a;
    --paper: #ffffff;
  }
  * { box-sizing: border-box; margin: 0; padding: 0; }
  html, body { width: 1200px; height: 1012px; overflow: hidden; background: var(--paper); }
  body { position: relative; font-family: "Open Sans", sans-serif; color: var(--ink); }

  .brand-mark {
    position: absolute; left: 518px; top: 40px; width: 164px; height: 164px;
    background: var(--mark-dark);
  }
  .brand-name {
    position: absolute; left: 0; width: 1200px; top: 216px; text-align: center;
    font-family: "Oswald", sans-serif; font-weight: 400; font-size: 31px; letter-spacing: 0.3px; line-height: 44px;
  }

  .rule {
    position: absolute; left: 48px; width: 1111px; height: 2px;
    background: linear-gradient(to right, rgba(201,195,162,0), var(--rule) 30%, var(--rule) 70%, rgba(201,195,162,0));
  }
  .rule--nav-top { top: 276px; }
  .rule--nav-bottom { top: 331px; }
  .rule--foot-top { top: 925px; }
  .rule--foot-bottom { top: 979px; }

  .main-nav { position: absolute; top: 290px; left: 0; width: 1200px; height: 30px; }
  .main-nav a {
    position: absolute; transform: translateX(-50%); text-decoration: none; color: var(--ink);
    font-family: "Oswald", sans-serif; font-weight: 300; font-size: 20px; letter-spacing: 0.5px; line-height: 30px;
  }
  .main-nav a.is-current { color: var(--gold); }

  .contact-item { position: absolute; top: 366px; width: 300px; margin-left: -150px; text-align: center; }
  .contact-item svg { display: block; margin: 0 auto; height: 30px; width: 30px; fill: var(--icon); }
  .contact-item h2 {
    margin-top: 18px; font-weight: 600; font-size: 21px; letter-spacing: 2px; line-height: 26px;
  }
  .contact-item p { margin-top: 10px; font-size: 12.5px; letter-spacing: 0.8px; color: var(--muted); }
  .contact-item p.is-dark { color: var(--ink); }

  .contact-form { position: absolute; left: 335px; top: 513px; width: 518px; }
  .field {
    display: block; width: 518px; height: 42px; margin-bottom: 19px; padding: 0 17px;
    border: 2px solid var(--field-border); background: var(--paper);
    font-family: "Nunito", sans-serif; font-size: 14px; color: var(--muted);
  }
  .field--message { height: 148px; padding-top: 15px; resize: vertical; margin-bottom: 21px; }
  .field::placeholder { color: #777777; }
  .send-button {
    display: block; width: 113px; height: 44px; border: 0; background: #000000; color: #ffffff;
    font-family: "Montserrat", sans-serif; font-weight: 700; font-size: 10px; letter-spacing: 1.2px;
  }

  .social-links { position: absolute; top: 884px; left: 0; width: 1200px; height: 22px; }
  .social-links a {
    position: absolute; transform: translateX(-50%); text-decoration: none; color: var(--ink);
    display: flex; align-items: center; gap: 5px;
    font-family: "Open Sans", sans-serif; font-size: 12px; line-height: 22px;
  }
  .social-dot { width: 7px; height: 7px; border-radius: 50%; background: var(--ink); }

  .site-footer {
    position: absolute; top: 937px; left: 0; width: 1200px; text-align: center;
    font-family: "Oswald", sans-serif; font-weight: 300; font-size: 17px; line-height: 30px;
  }
</style>
</head>
<body>
  <header class="site-header">
    <div class="brand-mark" aria-hidden="true"></div>
    <h1 class="brand-name">Maren Holloway</h1>
  </header>

  <div class="rule rule--nav-top"></div>
  <nav class="main-nav">
    <a href="#" style="left:471px">HOME</a>
    <a href="#" style="left:586px">ABOUT ME</a>
    <a href="#" class="is-current" style="left:713px">CONTACT</a>
  </nav>
  <div class="rule rule--nav-bottom"></div>

  <main>
    <section class="contact-item" style="left:256px">
      <svg viewBox="0 0 24 24" aria-hidden="true"><path d="M12 1.5c-4.4 0-7.5 3.2-7.5 7.4 0 5 7.5 14.1 7.5 14.1s7.5-9.1 7.5-14.1c0-4.2-3.1-7.4-7.5-7.4zm0 9.6a2.2 2.2 0 1 1 0-4.4 2.2 2.2 0 0 1 0 4.4z"/></svg>
      <h2>ADDRESS</h2>
      <p>48 Linden Row, Hudson (USA)</p>
    </section>
    <section class="contact-item" style="left:590px">
      <svg viewBox="0 0 24 24" aria-hidden="true"><path d="M6.6 2.2l3 3.3c.5.6.5 1.4 0 2L8 9.1c1.3 2.8 3.6 5.1 6.4 6.5l1.7-1.6c.6-.5 1.4-.5 2 0l3.3 3c.6.6.6 1.5 0 2.1l-2 2c-.8.8-2.1 1-3.2.5C9.9 19.1 4.9 14.1 2.4 7.8c-.4-1.1-.2-2.4.6-3.2l1.6-2.4c.6-.6 1.5-.6 2 0z"/></svg>
      <h2>PHONE</h2>
      <p>+1 555 014 228</p>
    </section>
    <section class="contact-item" style="left:924px">
      <svg viewBox="0 0 24 24" aria-hidden="true"><path d="M12 2.5l9 5.3V19a2 2 0 0 1-2 2H5a2 2 0 0 1-2-2V7.8l9-5.3zm0 11.2l7.2-4.8L12 4.8 4.8 8.9 12 13.7z"/></svg>
      <h2>EMAIL</h2>
      <p class="is-dark">hello@marenholloway.art</p>
    </section>

    <form class="contact-form" action="#">
      <input class="field" type="text" placeholder="Your Name">
      <input class="field" type="email" placeholder="Your Email">
      <textarea class="field field--message" placeholder="Message"></textarea>
      <button class="send-button" type="submit">SEND</button>
    </form>

    <div class="social-links">
      <a href="#" style="left:518px"><span class="social-dot"></span>Pinwall</a>
      <a href="#" style="left:590px"><span class="social-dot"></span>Chirper</a>
      <a href="#" style="left:662px"><span class="social-dot"></span>Lensly</a>
    </div>
  </main>

  <div class="rule rule--foot-top"></div>
  <footer class="site-footer">Copyright 2022, Maren Holloway</footer>
  <div class="rule rule--foot-bottom"></div>
</body>
</html>
```